Front and content page design for Fitness Cookbook

I am looking for someone to Design a front cover for a Recipe book and also create an amazing layout for the book.

Its for a corporate seminar so has to be eye catching, professional and bold.

Content is complete

Target Market(s)

Industry/Entity Type

Health And Wellness

Font styles to use
Sans Serif

Requirements
Must have
• Eye catching, professional and bold.
• By Dorian as stated on the document
• Must have Tidewell Motion Logo on it.

```html
<!DOCTYPE html>
<html lang="en">
<head>
<meta charset="utf-8">
<title>Tuna Wraps – Tidewell Motion Cookbook</title>
<link href="https://fonts.googleapis.com/css2?family=Lato:wght@300;400;700&display=swap" rel="stylesheet">
<style>
  :root {
    --orange: #f39a1c;
    --ink: #2b2b2b;
    --paper: #ffffff;
    --photo-light: #e9ece6;
    --photo-green: #5f8f3a;
  }
  * { margin: 0; padding: 0; box-sizing: border-box; }
  html, body { width: 849px; height: 1200px; overflow: hidden; background: var(--paper); }
  body { font-family: "Lato", "Gill Sans", sans-serif; color: var(--ink); }
  .page { position: relative; width: 849px; height: 1200px; background: var(--paper); }
  .hero-photo {
    position: absolute; left: 0; top: 0; width: 849px; height: 467px;
    background: radial-gradient(ellipse at 55% 55%, var(--photo-green) 0%, #7aa84e 30%, #c9d6bd 55%, var(--photo-light) 75%);
  }
  .title-band {
    position: absolute; left: 0; top: 467px; width: 849px; height: 170px;
    background: var(--orange);
    display: flex; align-items: flex-end; justify-content: center; padding-bottom: 28px;
  }
  .title-band h1 { color: var(--paper); font-weight: 300; font-size: 70px; letter-spacing: 0.5px; }
  .recipe { position: absolute; left: 50px; top: 660px; width: 735px; font-size: 15.5px; line-height: 20px; }
  .label { color: var(--orange); font-weight: 700; text-transform: uppercase; }
  .label.heading { font-size: 17px; display: block; margin-top: 20px; }
  .timing span { font-weight: 400; }
  .ingredients { list-style: none; }
  .footer { position: absolute; right: 26px; bottom: 34px; display: flex; align-items: center; gap: 14px; font-size: 13px; color: var(--ink); }
  .brand { font-weight: 400; }
</style>
</head>
<body>
<div class="page">
  <div class="hero-photo" role="img" aria-label="Photo of lettuce wraps filled with tuna, tomato, cucumber and avocado on a white plate"></div>

  <div class="title-band"><h1>Tuna Wraps</h1></div>

  <section class="recipe">
    <p class="timing"><span class="label">Prep time</span> <span>10 mins</span></p>
    <p class="timing"><span class="label">Cooking time</span> <span>0 mins</span></p>

    <span class="label heading">Ingredients</span>
    <ul class="ingredients">
      <li>1 can tuna in brine or water (drained)</li>
      <li>1 carrot</li>
      <li>1 plum tomato</li>
      <li>1 mini cucumber</li>
      <li>1/4 red onion</li>
      <li>Large handful spinach</li>
      <li>1/2 avocado</li>
      <li>3 lettuce wraps</li>
      <li>1 tbsp extra virgin olive oil</li>
      <li>1 tbsp apple cider vinegar (optional)</li>
      <li>Salt, pepper &amp; paprika</li>
    </ul>

    <span class="label heading">Cooking instructions</span>
    <p class="method">Prepare the lettuce wraps ready to be filled. Cut up the carrot, cucumber, tomato, red onion and avocado into small pieces and put in a bowl. Drain the tuna and add it to the bowl along with the olive oil, vinegar and seasonings. Mix with your hands and fill each lettuce wrap with the tuna and vegetables.<br>(Can be made as a simple salad without the lettuce wraps)</p>
  </section>

  <footer class="footer">
    <span class="brand">Tidewell Motion</span>
    <span class="page-number">9</span>
  </footer>
</div>
</body>
</html>
```